Wesbite design for Investment Firm

We want a basic (clean) website that follows the form, fonts and colors of our attachments. This is for a financial investment management firm, but we have a boutique (anti-Wall Street) approach. Site should have an Home Page (Logo up top - room for basic copy on bottom, Philosophy Page (room for Quarterly Letter attachment and basic copy, Performance Page (room for Performance Overview and Performance Analysis and basic copy), Team Page, Commentary Page and Contact

Reason: Some designers have asked for an extension. Again, please only use image of Train Station or Train Station Logo in design.

Target Market(s)

Small and mid-size financial advisors from across the country

Industry/Entity Type

Financial

Number of Pages Required

5+ page

Font styles to use
Other font styles liked:
• Palotino Linotype

Colors
3176b5
cfdeed
ffffff

Requirements
Must have
• Please refer to existing site www.qlvor.example. Of note, this is too complex / cluttered. We simply want Blur, Grey and White consistent with attachments. The copy is pretty good, but will be simplified (and no quotes)
Should not have
• No images other than train station logo and / or train station image

```html
<!DOCTYPE html>
<html lang="en">
<head>
<meta charset="utf-8">
<title>Halden Crest Investment Company</title>
<link rel="stylesheet" href="https://fonts.googleapis.com/css2?family=Crimson+Text:wght@400;600&family=Tinos:wght@400&display=swap">
<style>
  :root {
    --navy: #0e2d62;
    --ink: #111111;
    --body-grey: #6a6a6a;
    --rule: #d6d6d6;
    --sketch-blue: #a9bcdc;
    --sketch-pale: #e6edf6;
    --white: #ffffff;
  }
  * { margin: 0; padding: 0; box-sizing: border-box; }
  html, body { width: 1200px; height: 843px; overflow: hidden; background: var(--white); }
  .page { position: relative; width: 1200px; height: 843px; font-family: "Crimson Text", serif; }

  .hero-art {
    position: absolute; left: 150px; top: 22px; width: 955px; height: 566px;
    border-radius: 50% 50% 50% 50% / 42% 42% 58% 58%;
    background: radial-gradient(ellipse at 58% 48%, var(--sketch-blue) 0%, #c6d4e9 38%, var(--sketch-pale) 62%, rgba(255,255,255,0) 74%);
  }

  .brand {
    position: absolute; left: 118px; top: 20px;
    font-family: "Crimson Text", serif; font-size: 28px; font-weight: 400;
    font-variant: small-caps; letter-spacing: 1px; color: var(--navy);
  }

  .phone { position: absolute; left: 961px; top: 21px; display: flex; align-items: center; gap: 10px; }
  .phone svg { display: block; }
  .phone-number { font-family: "Tinos", serif; font-size: 17px; color: var(--ink); }

  .main-nav { position: absolute; left: 101px; top: 83px; display: flex; gap: 0; }
  .main-nav a {
    font-family: "Crimson Text", serif; font-size: 17.5px; color: var(--ink);
    text-decoration: none; margin-right: 35px;
  }
  .main-nav a.is-current { color: var(--navy); }

  .intro { position: absolute; left: 140px; top: 581px; width: 920px; text-align: center; }
  .intro h1 {
    font-family: "Crimson Text", serif; font-weight: 400; font-size: 29px;
    color: var(--navy); margin-bottom: 26px;
  }
  .intro p {
    font-family: "Tinos", serif; font-size: 15px; line-height: 23px;
    color: var(--body-grey); margin-bottom: 17px;
  }

  .site-footer {
    position: absolute; left: 96px; top: 790px; width: 1007px;
    border-top: 1px solid var(--rule); text-align: center; padding-top: 14px;
    font-family: "Crimson Text", serif; font-size: 17px; color: var(--navy);
  }
</style>
</head>
<body>
<div class="page">
  <div class="hero-art" role="img" aria-label="Pale blue pencil sketch of an old railway station with a train beside the platform"></div>

  <div class="brand">Halden Crest Investment Company</div>

  <div class="phone">
    <svg width="30" height="29" viewBox="0 0 30 29" aria-hidden="true">
      <rect x="0.75" y="0.75" width="28.5" height="27.5" fill="none" stroke="var(--navy)" stroke-width="1.5"/>
      <path d="M10 8.5c.6-.6 1.4-.6 1.9 0l1.6 2c.4.5.3 1.2-.1 1.6l-1 1c.8 1.6 2 2.8 3.6 3.6l1-1c.4-.4 1.1-.5 1.6-.1l2 1.6c.6.5.6 1.3 0 1.9l-1.2 1.2c-.8.8-2 1-3 .5-3.2-1.5-5.7-4-7.2-7.2-.5-1-.3-2.2.5-3z" fill="var(--navy)"/>
    </svg>
    <span class="phone-number">555.014.7250</span>
  </div>

  <nav class="main-nav">
    <a href="#" class="is-current">Home</a>
    <a href="#">Our Philosophy</a>
    <a href="#">Performance</a>
    <a href="#">Our Team</a>
    <a href="#">Commentary</a>
    <a href="#">Contact</a>
  </nav>

  <section class="intro">
    <h1>We Are A Financial Investment Management Firm With A Boutique Approach.</h1>
    <p>We founded Halden Crest Investment Company in 1999, initially managing wealth from our family and friends in the town of Halden Crest. The high expectations of our original investors is a key contributor to our value driven investment philosophy.</p>
    <p>Based in Austin, TX, we manage assets for both individuals and institutions. Our investment methodology stresses absolute returns vs. relative performance, blending a combination of fundamental analysis, discipline and patience with the goal of preserving and compounding capital</p>
  </section>

  <footer class="site-footer">Copyright © 2017&nbsp; Halden Crest Investment Company.&nbsp; All Right Reserved.</footer>
</div>
</body>
</html>
```